RTavenor Business Cards & Letterhead

I have a logo but need a design for some new business cards. We are a Design-Build Firm that specializes in the design and construction of commercial projects.
the cards need to be professional. no cartoon stuff.
i would like to have the cards in AI format so I can update the card as needed. Logo is provided.
Our Address is: 4187 Marlowe Ct. Larkfield, New Calder 27614

```html
<!DOCTYPE html>
<html lang="en">
<head>
<meta charset="utf-8">
<title>RTavenor Business Cards</title>
<link rel="stylesheet" href="https://fonts.googleapis.com/css2?family=Montserrat:wght@400;500;700;800&display=swap">
<style>
  :root {
    --backdrop: #3a3a3c;
    --card-white: #ffffff;
    --card-dark: #1b1b1c;
    --ink: #353535;
    --ink-soft: #4a4a4a;
    --brand-blue: #0a6fb3;
    --brand-blue-deep: #0b5a94;
    --rule: #b9b9b9;
  }
  * { box-sizing: border-box; margin: 0; padding: 0; }
  html, body {
    width: 1200px; height: 1200px; overflow: hidden;
    background: var(--backdrop);
    font-family: "Montserrat", sans-serif;
  }
  .canvas { position: relative; width: 1200px; height: 1200px; }

  .card {
    position: absolute; left: 220px; width: 760px; height: 434px;
    border-radius: 40px; overflow: hidden;
    box-shadow: 0 14px 30px rgba(0,0,0,.35);
  }
  .card--front { top: 110px; background: var(--card-white); }
  .card--back  { top: 650px; background: var(--card-dark); }

  .card__bands { position: absolute; inset: 0; width: 100%; height: 100%; }

  .brand {
    position: absolute; display: flex; align-items: center; gap: 14px;
  }
  .brand__mark { width: 46px; height: 46px; background: var(--brand-blue); flex: none; }
  .brand__name {
    font-weight: 800; letter-spacing: 1px; line-height: 1;
    text-transform: uppercase;
  }
  .card--front .brand { left: 86px; top: 120px; }
  .card--front .brand__name { font-size: 70px; color: var(--ink); }
  .card--back .brand { left: 50%; top: 50%; transform: translate(-50%, -60%); }
  .card--back .brand__name { font-size: 80px; color: #ffffff; }
  .card--back .brand__mark { width: 54px; height: 54px; }

  .divider {
    position: absolute; left: 456px; top: 224px; width: 1px; height: 104px;
    background: var(--rule);
  }

  .contact { position: absolute; left: 482px; top: 214px; color: var(--ink-soft); font-size: 17px; font-weight: 500; }
  .contact__row { display: flex; align-items: flex-start; gap: 10px; margin-bottom: 8px; line-height: 1.25; }
  .contact__icon { width: 18px; height: 18px; flex: none; margin-top: 2px; }

  .person {
    position: absolute; left: 62px; top: 296px;
    border-left: 6px solid var(--brand-blue); padding-left: 12px;
  }
  .person__name { font-size: 34px; font-weight: 700; color: var(--brand-blue); line-height: 1; letter-spacing: .5px; }
  .person__role { font-size: 17px; font-weight: 400; color: var(--ink); letter-spacing: 1px; margin-top: 4px; }
</style>
</head>
<body>
<main class="canvas">

  <section class="card card--front" aria-label="Business card front">
    <svg class="card__bands" viewBox="0 0 760 434" preserveAspectRatio="none" aria-hidden="true">
      <defs>
        <linearGradient id="blueBand" x1="0" x2="1" y1="0" y2="0">
          <stop offset="0" stop-color="#0b5a94"/>
          <stop offset="1" stop-color="#0a78c0"/>
        </linearGradient>
      </defs>
      <polygon points="0,412 468,372 468,434 0,434" fill="url(#blueBand)"/>
      <polygon points="480,371 760,346 760,434 480,434" fill="#222223"/>
    </svg>

    <div class="brand">
      <span class="brand__mark"></span>
      <span class="brand__name">RTavenor</span>
    </div>

    <div class="divider"></div>

    <div class="contact">
      <div class="contact__row">
        <svg class="contact__icon" viewBox="0 0 24 24" aria-hidden="true"><path fill="#0a6fb3" d="M6.6 10.8a15.1 15.1 0 0 0 6.6 6.6l2.2-2.2c.3-.3.7-.4 1-.2 1.1.4 2.3.6 3.6.6.6 0 1 .4 1 1V20c0 .6-.4 1-1 1A17 17 0 0 1 3 4c0-.6.4-1 1-1h3.5c.6 0 1 .4 1 1 0 1.3.2 2.5.6 3.6.1.3 0 .7-.2 1z"/></svg>
        <span>(000) 000 0000</span>
      </div>
      <div class="contact__row">
        <svg class="contact__icon" viewBox="0 0 24 24" aria-hidden="true"><path fill="#0a6fb3" d="M2 5h20v14H2z"/><path fill="none" stroke="#fff" stroke-width="1.6" d="M2.5 5.5 12 13l9.5-7.5"/></svg>
        <span>email@company.com</span>
      </div>
      <div class="contact__row">
        <svg class="contact__icon" viewBox="0 0 24 24" aria-hidden="true"><path fill="none" stroke="#0a6fb3" stroke-width="2.4" d="M12 22s7-7 7-12a7 7 0 0 0-14 0c0 5 7 12 7 12z"/><circle cx="12" cy="10" r="2.5" fill="#0a6fb3"/></svg>
        <span>4187 Marlowe Ct. Larkfield<br>New Calder 27614</span>
      </div>
    </div>

    <div class="person">
      <p class="person__name">FULL NAME</p>
      <p class="person__role">POSITION</p>
    </div>
  </section>

  <section class="card card--back" aria-label="Business card back">
    <svg class="card__bands" viewBox="0 0 760 434" preserveAspectRatio="none" aria-hidden="true">
      <defs>
        <linearGradient id="blueStripe" x1="0" x2="1" y1="0" y2="0">
          <stop offset="0" stop-color="#0b5a94"/>
          <stop offset="1" stop-color="#0a7cc4"/>
        </linearGradient>
      </defs>
      <polygon points="378,370 688,370 670,400 360,400" fill="url(#blueStripe)"/>
    </svg>

    <div class="brand">
      <span class="brand__mark"></span>
      <span class="brand__name">RTavenor</span>
    </div>
  </section>

</main>
</body>
</html>
```